Trendy E Juice Product Labels Required

We are looking for design for an e Juice label line (the liquids used in electronic cigarettes). What we need is 5 product labels which eventually will be printed on 95mm x 40mm labels. Obviously the image will be created much larger than this but the aspect ratio should be scalable down to this size.

What each label must have is I would need is a background, a monster character, and space for a product name incorporated in to the design. The brand on this line is "Velvet Orbit". Whilst creatively, we are completely open to any concept, there is certain text which is necessary for incorporation in to each label. The attached file, "Example Label" shows these elements. NOTE: the attached file IS NOT a finished label.
Updates

Reason: Not received a design that we wish to proceed with.

Target Market(s)

25-35 year old vapers

Industry/Entity Type

Electronic

Requirements
Should not have
• Anything that may be construed as being targeted toward children.

```html
<!DOCTYPE html>
<html lang="en">
<head>
<meta charset="utf-8">
<title>Velvet Orbit – Oranges Label</title>
<link rel="stylesheet" href="https://fonts.googleapis.com/css2?family=Open+Sans:wght@400;600;700&family=Oswald:wght@500&family=Libre+Baskerville:wght@700&display=swap">
<style>
  :root {
    --page: #ebebeb;
    --teal: #1f5a6a;
    --lime: #d6dc3f;
    --white: #ffffff;
    --ink: #111111;
    --title-ink: #23393f;
    --alert-red: #e0262b;
    --burst-core: #fff4dc;
    --burst-edge: #f7c98a;
    --monster: #8a4a2a;
  }
  * { box-sizing: border-box; margin: 0; padding: 0; }
  html, body { width: 1200px; height: 1000px; overflow: hidden; background: var(--page); }
  body { position: relative; font-family: "Open Sans", Arial, sans-serif; color: var(--ink); }

  .label {
    position: absolute; left: 100px; top: 290px; width: 1000px; height: 421px;
    background: var(--white); overflow: hidden;
    box-shadow: 0 10px 30px rgba(0,0,0,.18);
  }
  .band-top { position: absolute; left: 0; top: 0; width: 100%; height: 25px; background: var(--teal); }
  .band-bottom { position: absolute; left: 0; bottom: 0; width: 100%; height: 28px; background: var(--teal); }
  .rule { position: absolute; left: 0; top: 264px; width: 100%; height: 6px; background: var(--ink); }
  .lower-field { position: absolute; left: 0; top: 270px; width: 100%; height: 123px; background: var(--lime); }

  .warning {
    position: absolute; left: 35px; top: 40px; width: 300px;
    text-align: center; text-transform: uppercase; font-size: 13.4px; line-height: 17.5px;
  }
  .warning h2, .ingredients h2 { font-size: 13.4px; font-weight: 700; }

  .ingredients {
    position: absolute; left: 35px; top: 290px; width: 300px;
    text-align: center; text-transform: uppercase; font-size: 13.4px; line-height: 18px;
  }

  .character-art {
    position: absolute; left: 330px; top: 25px; width: 330px; height: 239px;
    background: radial-gradient(ellipse at 50% 75%, var(--burst-core) 0%, var(--burst-core) 25%, var(--burst-edge) 55%, rgba(255,255,255,0) 80%);
  }
  .character-art::after {
    content: ""; position: absolute; left: 80px; top: 45px; width: 170px; height: 180px;
    border-radius: 50% 50% 40% 40%;
    background: radial-gradient(circle at 50% 45%, #a8603a, var(--monster));
    opacity: .9;
  }

  .name-banner {
    position: absolute; left: 332px; top: 250px; width: 312px; height: 84px;
    background: var(--white); border: 5px solid var(--ink);
    display: flex; align-items: center; justify-content: center;
  }
  .name-banner h1 {
    font-family: "Oswald", "Arial Narrow", sans-serif; font-weight: 500;
    font-size: 46px; letter-spacing: .5px; color: var(--ink); text-transform: uppercase;
  }

  .flavour {
    position: absolute; left: 352px; top: 345px; width: 291px; padding-bottom: 6px;
    border-bottom: 1.5px solid var(--title-ink);
    text-align: center; font-family: "Libre Baskerville", Georgia, serif; font-weight: 700;
    font-size: 24px; color: var(--title-ink); text-transform: uppercase;
  }

  .web { position: absolute; left: 730px; top: 38px; width: 200px; text-align: center; font-size: 13.4px; font-weight: 700; }
  .social { position: absolute; left: 730px; top: 62px; }
  .handle { position: absolute; left: 730px; top: 131px; width: 200px; text-align: center; font-size: 12.5px; font-weight: 700; }

  .distributor {
    position: absolute; left: 717px; top: 158px; width: 258px; height: 89px;
    background: var(--lime); border: 3px solid var(--ink); border-radius: 10px;
    display: flex; align-items: center; justify-content: center;
    text-align: center; text-transform: uppercase; font-size: 14.5px; font-weight: 700; line-height: 19px;
  }

  .safety { position: absolute; left: 740px; top: 300px; }
  .alert { position: absolute; left: 862px; top: 282px; }
</style>
</head>
<body>
  <main class="label">
    <div class="band-top"></div>
    <div class="lower-field"></div>
    <div class="rule"></div>
    <div class="band-bottom"></div>

    <section class="warning">
      <h2>Warning</h2>
      <p>This product contains nicotine, a substance which is knows to cause birth defects. Do not swallow. Avoid contact with skin. Keep out of reac of children and pets. This product is intended for use by oersons 18 and older. Pregant women and those breast feeding should not use this product. May contain traces of nuts.</p>
    </section>

    <section class="ingredients">
      <h2>Ingredients</h2>
      <p>USP/EP Propelyn Slycil (XX%), USP/EP Vegetable Glycerrin (XX%), USP/EP Nicotine, natural and artificial flavorings.</p>
    </section>

    <div class="character-art" role="img" aria-label="Monster character with eye stalks and a wide toothy grin over an orange sunburst, with three teal stars"></div>

    <div class="name-banner"><h1>Velvet Orbit</h1></div>
    <p class="flavour">Oranges</p>

    <p class="web">WWW.DOMAINNAME.COM</p>
    <svg class="social" width="200" height="64" viewBox="0 0 200 64" aria-label="Social channels">
      <circle cx="31" cy="31" r="27" fill="none" stroke="#111" stroke-width="2.5"/>
      <circle cx="99" cy="31" r="27" fill="none" stroke="#111" stroke-width="2.5"/>
      <circle cx="167" cy="31" r="27" fill="none" stroke="#111" stroke-width="2.5"/>
    </svg>
    <p class="handle">@USERNAME</p>

    <div class="distributor"><p>Distributed by<br>Company Name &amp; Address<br>Telephone</p></div>

    <svg class="safety" width="110" height="75" viewBox="0 0 110 75" aria-label="Safety symbols">
      <g fill="none" stroke="#e0262b" stroke-width="2.5">
        <circle cx="16" cy="17" r="13"/><line x1="7" y1="8" x2="25" y2="26"/>
        <circle cx="94" cy="17" r="13"/><line x1="85" y1="8" x2="103" y2="26"/>
        <circle cx="16" cy="57" r="13"/>
        <circle cx="94" cy="57" r="13"/>
      </g>
      <path d="M12 21v-8h8v8M16 10v-2" stroke="#111" stroke-width="2" fill="none"/>
      <path d="M94 9v16M90 14h8" stroke="#111" stroke-width="2" fill="none"/>
      <path d="M10 60l6-9 6 9z" stroke="#111" stroke-width="1.8" fill="none"/>
      <text x="94" y="63" text-anchor="middle" font-family="Open Sans, Arial, sans-serif" font-weight="700" font-size="16" fill="#111">18</text>
      <path d="M55 22l16 27H39z" fill="none" stroke="#111" stroke-width="2.5" stroke-linejoin="round"/>
      <line x1="55" y1="31" x2="55" y2="40" stroke="#111" stroke-width="2.5"/>
      <circle cx="55" cy="44.5" r="1.6" fill="#111"/>
    </svg>

    <svg class="alert" width="100" height="100" viewBox="0 0 100 100" aria-label="Warning triangle">
      <path d="M50 6l45 88H5z" fill="none" stroke="#e0262b" stroke-width="4" stroke-linejoin="miter"/>
    </svg>
  </main>
</body>
</html>
```